Marwick Law Letterhead

We need a new letterhead design for a Law Firm. The address for the law firm is 1475 Calloway Street, Suite 210, Houston, Texas 77041. Phone Number: 832-361-9027; Fax Number: 832-614-7359. The logo is uploaded to the project.

```html
<!DOCTYPE html>
<html lang="en">
<head>
<meta charset="utf-8">
<title>Marwick Law Letterhead</title>
<link rel="stylesheet" href="https://fonts.googleapis.com/css2?family=Arimo:wght@400;700&family=Libre+Baskerville:wght@400;700&display=swap">
<style>
  :root {
    --backdrop: #e8e5e0;
    --paper: #ffffff;
    --ink: #1a1a1a;
    --navy: #1d3266;
    --crimson: #b81d27;
    --signature-tone: #d9d9dc;
  }
  * { box-sizing: border-box; margin: 0; padding: 0; }
  html, body {
    width: 1200px;
    height: 900px;
    overflow: hidden;
    background: var(--backdrop);
  }
  .letterhead {
    position: absolute;
    left: 267px;
    top: 20px;
    width: 665px;
    height: 860px;
    background: var(--paper);
    box-shadow: 0 4px 18px rgba(0,0,0,0.15);
    font-family: "Arimo", Arial, sans-serif;
    color: var(--ink);
  }
  .brand {
    position: absolute;
    left: 470px;
    top: 52px;
    display: flex;
    align-items: center;
    gap: 10px;
  }
  .brand-mark {
    width: 14px;
    height: 14px;
    background: var(--crimson);
  }
  .brand-name {
    font-family: "Libre Baskerville", Georgia, serif;
    font-weight: 700;
    font-size: 24px;
    color: var(--navy);
    letter-spacing: 0.5px;
  }
  .letter {
    position: absolute;
    left: 69px;
    top: 154px;
    width: 528px;
    font-size: 12.6px;
    line-height: 20.5px;
  }
  .letter-date { margin-bottom: 33px; }
  .recipient { margin-bottom: 40px; }
  .recipient-name { font-weight: 700; font-size: 14px; }
  .body-paragraph {
    text-align: justify;
    margin-bottom: 20.5px;
  }
  .body-paragraph.last { margin-bottom: 0; }
  .signature {
    display: block;
    width: 86px;
    height: 22px;
    margin-top: 40px;
    background: var(--signature-tone);
    border-radius: 11px;
  }
  .sender-name {
    margin-top: 8px;
    font-size: 15.5px;
    font-weight: 700;
  }
  .contact {
    position: absolute;
    left: 430px;
    top: 744px;
    font-family: "Libre Baskerville", Georgia, serif;
    font-weight: 700;
    font-size: 9px;
    color: var(--navy);
    letter-spacing: 0.8px;
  }
  .contact-line {
    display: flex;
    align-items: center;
    gap: 5px;
    height: 20px;
  }
  .contact-line svg { width: 10px; height: 10px; fill: var(--crimson); }
  .contact-address {
    margin-top: 4px;
    line-height: 13px;
    letter-spacing: 0.5px;
  }
  .footer-band {
    position: absolute;
    left: 430px;
    right: 0;
    bottom: 0;
    height: 25px;
  }
  .footer-band .stripe-red {
    height: 4px;
    background: var(--crimson);
  }
  .footer-band .stripe-navy {
    margin-top: 2px;
    height: 19px;
    background: var(--navy);
  }
</style>
</head>
<body>
  <main class="letterhead">
    <header class="brand">
      <span class="brand-mark"></span>
      <span class="brand-name">Marwick Law</span>
    </header>

    <section class="letter">
      <p class="letter-date">4th September 20XX</p>

      <div class="recipient">
        <p class="recipient-name">Ronny Reader</p>
        <p>CEO, Company Name</p>
        <p>123 Address St</p>
        <p>Anytown, ST 12345</p>
      </div>

      <p>Dear Mr. Reader,</p>
      <p class="body-paragraph">Lorem ipsum dolor sit amet, consectetuer adipiscing elit, sed diam nonummy nibh euismod tincidunt ut laoreet dolore magna aliquam erat volutpat. Ut wisi enim ad minim veniam, quis nostrud exerci tation ullamcorper suscipit lobortis nisl ut aliquip ex ea commodo consequat.</p>
      <p class="body-paragraph">Duis autem vel eum iriure dolor in hendrerit in vulputate velit esse molestie consequat, vel illum dolore eu feugiat nulla facilisis at vero eros et accumsan.</p>
      <p class="body-paragraph last">Nam liber tempor cum soluta nobis eleifend option congue nihil imperdiet doming id quod mazim placerat facer possim assum. Typi non habent claritatem insitam; est usus legentis in iis qui facit eorum claritatem. Investigationes demonstraverunt lectores legere me lius quod ii legunt saepius.</p>
      <p>Sincerely,</p>

      <span class="signature" role="img" aria-label="Handwritten signature of the sender"></span>
      <p class="sender-name">Your Name</p>
    </section>

    <footer class="contact">
      <p class="contact-line">
        <svg viewBox="0 0 24 24" aria-hidden="true"><path d="M6.6 10.8a15.1 15.1 0 0 0 6.6 6.6l2.2-2.2c.3-.3.7-.4 1-.2 1.1.4 2.3.6 3.6.6.6 0 1 .4 1 1V20c0 .6-.4 1-1 1C10.6 21 3 13.4 3 4c0-.6.4-1 1-1h3.5c.6 0 1 .4 1 1 0 1.3.2 2.5.6 3.6.1.3 0 .7-.2 1z"/></svg>
        <span>832-361-9027</span>
      </p>
      <p class="contact-line">
        <svg viewBox="0 0 24 24" aria-hidden="true"><path d="M7 3h8l3 3v4H7zM4 10h16a2 2 0 0 1 2 2v7a2 2 0 0 1-2 2H4a2 2 0 0 1-2-2v-7a2 2 0 0 1 2-2zm2 4v2h5v-2zm8 0v2h2v-2zm3 0v2h2v-2z"/></svg>
        <span>832-614-7359</span>
      </p>
      <p class="contact-address">1475 Calloway Street,<br>Suite 210,<br>Houston, Texas 77041</p>
    </footer>

    <div class="footer-band" aria-hidden="true">
      <div class="stripe-red"></div>
      <div class="stripe-navy"></div>
    </div>
  </main>
</body>
</html>
```